Its time for a new website

We are at a point now where we are in desperate need of a new website. It was last updated 2006 but still looks like its 1995. We are looking for something eye catching to our clients but easy to navigate and add/remove photos of jobs/trucks and information. Our key business is the manufacture of fire appliances and resale of parts and equipment.

www.kestrelrigs.com.au

Coding

Coded - Design and coding required

Number of Pages Required

5+ page

Requirements
Must have
• Logo

```html
<!DOCTYPE html>
<html lang="en">
<head>
<meta charset="utf-8">
<title>Kestrel Rigs</title>
<link href="https://fonts.googleapis.com/css2?family=Audiowide&family=Open+Sans:ital,wght@0,400;0,600;0,700;1,400&display=swap" rel="stylesheet">
<style>
:root{
  --red:#d2141b;
  --blue:#1570bd;
  --ink:#333;
  --muted:#666;
  --light:#f2f2f2;
  --white:#fff;
}
*{box-sizing:border-box;margin:0;padding:0}
html,body{width:802px;height:1200px;overflow:hidden;background:var(--white)}
body{font-family:"Open Sans",sans-serif;color:var(--ink);position:relative}
.display{font-family:"Audiowide",sans-serif;font-weight:400}

.topline{position:absolute;top:0;left:0;width:802px;height:3px;background:var(--red)}
.header{position:absolute;top:3px;left:0;width:802px;height:95px}
.brand{position:absolute;left:68px;top:20px;display:flex;align-items:center;gap:8px}
.brand-dot{width:44px;height:44px;border-radius:50%;background:var(--red)}
.brand-name{font-family:"Audiowide",sans-serif;font-size:17px;color:var(--blue)}
.contact{position:absolute;top:32px;display:flex;gap:10px}
.contact .ico{width:31px;height:31px;border:1.5px solid var(--red);border-radius:50%;display:flex;align-items:center;justify-content:center}
.contact small{display:block;font-size:7.5px;color:#444;margin-bottom:3px}
.contact p{font-size:10px;color:var(--red);line-height:15px}
.c-addr{left:432px}
.c-phone{left:625px}

.nav{position:absolute;top:98px;left:0;width:802px;height:34px;background:linear-gradient(#e3161e,#b50d13)}
.nav ul{position:absolute;left:66px;top:0;display:flex;list-style:none;height:34px}
.nav li{font-size:8.5px;font-weight:700;color:var(--white);display:flex;align-items:center;padding:0 13.5px;border-right:1px solid rgba(0,0,0,.18)}
.nav li.active{background:var(--blue);padding:0 22px}

.hero{position:absolute;top:132px;left:0;width:802px;height:320px;background:linear-gradient(160deg,#6a5a4a 0%,#c29a6a 35%,#8a6a4c 60%,#3b2f26 100%)}
.hero h1{position:absolute;top:88px;width:802px;text-align:center;font-family:"Audiowide",sans-serif;font-size:20px;line-height:30px;color:var(--white);font-weight:400}
.hero p{position:absolute;top:153px;left:225px;width:320px;font-size:8px;line-height:16px;color:var(--white)}
.hero .btns{position:absolute;top:194px;width:802px;display:flex;justify-content:center;gap:13px}
.btn{display:inline-flex;align-items:center;justify-content:center;width:97px;height:27px;font-size:8.5px;font-weight:700;color:var(--white);background:linear-gradient(#e01a21,#b80f15);border-radius:2px}
.btn.blue{background:var(--blue)}
.arrow{position:absolute;top:130px}

.welcome{position:absolute;top:452px;left:0;width:802px;height:195px;text-align:center}
.welcome h2{margin-top:28px;font-size:20px;color:#333}
.r{color:var(--red)}.b{color:var(--blue)}
.lead{font-size:9px;font-style:italic;color:var(--muted);margin-top:10px}
.welcome .body{width:520px;margin:7px auto 0;font-size:7.5px;line-height:15px;color:#444}
.welcome .btn{margin-top:10px}

.services{position:absolute;top:647px;left:0;width:802px;height:328px;background:var(--light);text-align:center}
.services h2{margin-top:32px;font-size:20px;color:#333}
.services .lead{margin-top:8px}
.cards{position:absolute;left:66px;top:95px;display:flex;gap:21px}
.card{width:151px}
.card .photo{height:107px}
.card h3{font-size:10px;font-weight:600;margin-top:9px;letter-spacing:.3px}
.card p{font-size:7px;line-height:15px;color:#555;margin-top:3px;height:30px;padding:0 8px}
.card .btn{margin-top:5px}

.news{position:absolute;top:975px;left:66px;width:680px}
.news h2{font-size:20px;margin-top:14px}
.items{display:flex;margin-top:10px}
.item{width:344px;flex:none;display:flex;gap:10px}
.item .photo{width:98px;height:77px;flex:none}
.item .text{width:205px}
.item h4{font-size:10px;font-weight:600;margin-top:1px;white-space:nowrap}
.item .date{font-size:7px;color:#555;margin-top:8px;display:flex;align-items:center;gap:4px}
.item p{font-size:7px;line-height:14px;color:#555;margin-top:5px}

.footer{position:absolute;top:1136px;left:0;width:802px;height:64px;background:linear-gradient(#d8141b,#a30c11);color:var(--white)}
.links{position:absolute;left:65px;top:15px;font-size:7.5px}
.social{position:absolute;left:65px;top:34px;display:flex;gap:4px}
.social span{width:19px;height:19px;border:1px solid rgba(255,255,255,.85);border-radius:50%}
.copy{position:absolute;left:579px;top:27px;font-size:7.5px}
.code{position:absolute;left:764px;top:27px;font-size:7.5px}
</style>
</head>
<body>
<div class="topline"></div>

<header class="header">
  <div class="brand"><span class="brand-dot"></span><span class="brand-name">Kestrel Rigs</span></div>
  <div class="contact c-addr">
    <div class="ico"><svg width="12" height="14" viewBox="0 0 12 14"><path d="M6 13C2 8 1 6 1 4.8A5 5 0 0 1 11 4.8C11 6 10 8 6 13Z" fill="none" stroke="#d2141b" stroke-width="1.4"/><circle cx="6" cy="5" r="1.6" fill="#d2141b"/></svg></div>
    <div><small>Address :</small><p>Unit 9 Banksia Lane Harwood<br>6418 Western Australia</p></div>
  </div>
  <div class="contact c-phone">
    <div class="ico"><svg width="12" height="12" viewBox="0 0 12 12"><path d="M2 1l2 0 1 3-1.5 1a7 7 0 0 0 3.5 3.5L8 7l3 1v2a1 1 0 0 1-1 1A9 9 0 0 1 1 2a1 1 0 0 1 1-1Z" fill="#d2141b"/></svg></div>
    <div><small>Toll Free:</small><p>08 95550137</p></div>
  </div>
</header>

<nav class="nav">
  <ul>
    <li class="active">HOME</li><li>ABOUT US</li><li>PUMPERS TANKERS</li><li>GPA/RESCUE</li><li>LIGHT TANKERS</li><li>TARILERS</li><li>SLIP-ON UNITS</li><li>CONTACT US</li>
  </ul>
</nav>

<section class="hero" role="img" aria-label="Welder grinding steel with sparks flying">
  <svg class="arrow" style="left:28px" width="12" height="36" viewBox="0 0 12 36"><path d="M11 1 1 18 11 35" fill="none" stroke="rgba(255,255,255,.6)"/></svg>
  <svg class="arrow" style="left:762px" width="12" height="36" viewBox="0 0 12 36"><path d="M1 1 11 18 1 35" fill="none" stroke="rgba(255,255,255,.6)"/></svg>
  <h1>Kestrel Rigs manufacture quality<br>fire truck and tender</h1>
  <p>Confident in KRS's ability to enhance your organization as well, upon request, a full copy of Martin's impressive resume, which contains more detailed information</p>
  <div class="btns"><span class="btn blue">NEW FOR 2006</span><span class="btn">READ MORE</span></div>
</section>

<section class="welcome">
  <h2 class="display">Welcome to <span class="r">Kestrel</span> <span class="b">Rigs</span></h2>
  <p class="lead">Kestrel Rigs are Western Australia's leading manufacturer of custom firefighting equipment</p>
  <p class="body">Lorem Ipsum is simply dummy text of the printing and typesetting industry. Lorem Ipsum has been the industry's standard dummy text ever since the 1500s, when an unknown printer took a galley of type and scrambled it to make a type specimen book. It has survived not only five centuries, but also the leap into electronic typesetting, remaining essentially unchanged.</p>
  <span class="btn">READ MORE</span>
</section>

<section class="services">
  <h2 class="display">Our <span class="r">S</span><span class="b">ervices</span></h2>
  <p class="lead">Lorem Ipsum is simply dummy text of the printing and typesetting industry. Lorem Ipsum has been the industry's</p>
  <svg style="position:absolute;left:18px;top:140px" width="8" height="18" viewBox="0 0 8 18"><path d="M7 1 1 9 7 17" fill="none" stroke="#bbb"/></svg>
  <svg style="position:absolute;left:758px;top:140px" width="8" height="18" viewBox="0 0 8 18"><path d="M1 1 7 9 1 17" fill="none" stroke="#bbb"/></svg>
  <div class="cards">
    <div class="card"><div class="photo" role="img" aria-label="Red pumper fire truck" style="background:linear-gradient(#b9c6cf,#c0242a 55%,#555)"></div><h3>PUMPERS</h3><p>Our range of pumpers have been specifically designed for use in a broad</p><span class="btn">READ MORE</span></div>
    <div class="card"><div class="photo" role="img" aria-label="Red tanker truck" style="background:linear-gradient(#a9b6c0,#b9222a 55%,#6a6a6a)"></div><h3>TANKERS</h3><p>We manufacture a wide range of Rural Tankers&nbsp; which differ from each other</p><span class="btn">READ MORE</span></div>
    <div class="card"><div class="photo" role="img" aria-label="GPA rescue truck" style="background:linear-gradient(#c8cdd2,#d6383c 50%,#e8e8e8 75%,#444)"></div><h3>GPA RESCUE</h3><p>Lorem Ipsum is simply dummy text of the printing and typesetting industry.</p><span class="btn">READ MORE</span></div>
    <div class="card"><div class="photo" role="img" aria-label="White light tanker utility vehicle" style="background:linear-gradient(#8fb0c8,#6f7c5a 40%,#eee 70%,#b09a78)"></div><h3>LIGHT TANKERS</h3><p>Our range of Light Tanker fast attacks are available on Tarvo, Quendal,.</p><span class="btn">READ MORE</span></div>
  </div>
</section>

<section class="news">
  <h2 class="display">Latest <span class="r">N</span><span class="b">ews</span></h2>
  <div class="items">
    <div class="item"><div class="photo" role="img" aria-label="Metal cutting with sparks" style="background:linear-gradient(135deg,#3a4450,#c9a070 55%,#2e3238)"></div>
      <div class="text"><h4>Finibus Bonorum Malorm ducimus</h4><div class="date"><svg width="9" height="9" viewBox="0 0 9 9"><rect x=".5" y="1.5" width="8" height="7" fill="none" stroke="#888"/><path d="M.5 3.5h8" stroke="#888"/></svg>October 20,2014</div><p>Lorem Ipsum is simply dummy text of the printing and typesetting industry. Lorem Ipsum has been the industry's standard dummy text ever since the 1500s.</p></div></div>
    <div class="item"><div class="photo" role="img" aria-label="Worker operating a green sheet metal machine" style="background:linear-gradient(90deg,#4a4f55,#3f8a4a 50%,#b8bcc0)"></div>
      <div class="text"><h4>Voluptatem accusantium doloremque</h4><div class="date"><svg width="9" height="9" viewBox="0 0 9 9"><rect x=".5" y="1.5" width="8" height="7" fill="none" stroke="#888"/><path d="M.5 3.5h8" stroke="#888"/></svg>October 20,2014</div><p>Lorem Ipsum is simply dummy text of the printing and typesetting industry. Lorem Ipsum has been the industry's standard dummy text ever since the 1500s.</p></div></div>
  </div>
</section>

<footer class="footer">
  <div class="links">Privacy Policy |&nbsp; Store Locator |&nbsp; Advanced Search |&nbsp; Terms &amp; Conditions</div>
  <div class="social"><span></span><span></span><span></span><span></span><span></span></div>
  <div class="copy">Copyrights © 2015 Kestrel Rigs. All rights reserved.</div>
  <div class="code">C12</div>
</footer>
</body>
</html>
```